creating a certificate for our flagship course

Hi,
We need a new certificate for our flagship course called Silver Harbour. We have been running this course for 25 years this year and want to get something special that represents that. We need our logos incorporated and we love to have a compass or Koru incorporated in the certificate. We like something different from your standard certificate, but not too crazy.

The text should say something along the lines of:
This certificate is awarded to ....
For successfully completing and contributing to the three day Silver Harbour programme.

signed:... date:...

to learn a bit more about this course and our company, please check our website. www.mellorquaid.co.nz

Thank you!

Target Market(s)

attendees who completed our 3 day programme.

Requirements
Must have
• Both our SH logo and our brand logo. a compass or a koru.
• a 25th year existence something on it.

```html
<!DOCTYPE html>
<html lang="en">
<head>
<meta charset="utf-8">
<title>Silver Harbour – Certificate of Completion</title>
<link rel="stylesheet" href="https://fonts.googleapis.com/css2?family=Montserrat:wght@600&family=Open+Sans:wght@400;600;700&family=Great+Vibes&display=swap">
<style>
  :root {
    --navy: #3d3e52;
    --navy-light: #6e6f85;
    --silver: #8e8f9c;
    --gold: #c99a2e;
    --script-gold: #b7862c;
    --ink: #3a3a4c;
    --ink-strong: #1f1f2a;
    --rule: #a9a9b3;
    --paper: #ffffff;
    --pattern: #dcdce4;
    --brand-green: #8cc152;
    --brand-slate: #6b6c7c;
  }
  * { margin: 0; padding: 0; box-sizing: border-box; }
  html, body { width: 928px; height: 1200px; overflow: hidden; background: var(--paper); }
  .certificate {
    position: relative;
    width: 928px;
    height: 1200px;
    background: var(--paper);
    font-family: "Open Sans", Arial, sans-serif;
    color: var(--ink);
  }
  .certificate__frame { position: absolute; inset: 0; }
  .certificate__title {
    position: absolute; left: 0; right: 0; top: 40px;
    text-align: center; color: #fff;
    font-family: "Montserrat", Arial, sans-serif; font-weight: 600;
    font-size: 72px; letter-spacing: 9px; line-height: 1;
    text-shadow: 0 2px 4px rgba(0,0,0,.35);
  }
  .certificate__subtitle {
    position: absolute; left: 0; right: 0; top: 121px;
    text-align: center; color: #fff;
    font-family: "Montserrat", Arial, sans-serif; font-weight: 600;
    font-size: 36px; letter-spacing: 2px; line-height: 1;
    text-shadow: 0 2px 3px rgba(0,0,0,.3);
  }
  .certificate__anniversary {
    position: absolute; left: 272px; top: 268px; width: 590px;
    text-align: center;
    font-family: "Great Vibes", cursive;
    font-size: 80px; color: var(--script-gold); line-height: 1;
    transform: rotate(-10deg);
  }
  .course-mark {
    position: absolute; left: 153px; top: 475px;
    display: flex; align-items: center; gap: 35px;
  }
  .course-mark__square { width: 175px; height: 175px; background: var(--brand-green); }
  .course-mark__name { font-size: 62px; font-weight: 400; color: var(--ink); letter-spacing: -0.5px; }
  .award__lead {
    position: absolute; left: 0; right: 0; top: 714px;
    text-align: center; font-size: 23px; font-weight: 600; letter-spacing: .2px;
  }
  .award__recipient {
    position: absolute; left: 0; right: 0; top: 766px;
    text-align: center; font-size: 37px; font-weight: 700; color: var(--ink-strong);
  }
  .award__rule { position: absolute; height: 1.5px; background: var(--rule); }
  .award__rule--long { left: 120px; width: 688px; top: 828px; }
  .award__rule--short { left: 291px; width: 349px; top: 837px; background: #9d9daa; }
  .award__reason {
    position: absolute; left: 0; right: 0; top: 866px;
    text-align: center; font-size: 20.5px; line-height: 28px;
  }
  .company-mark {
    position: absolute; left: 314px; top: 1012px;
    display: flex; align-items: center; gap: 18px;
  }
  .company-mark__square { width: 64px; height: 64px; background: var(--brand-slate); }
  .company-mark__name { font-size: 23px; font-weight: 400; color: var(--ink); line-height: 27px; letter-spacing: 1.5px; }
  .sign-off { position: absolute; top: 1129px; font-size: 18px; font-weight: 600; display: flex; align-items: flex-end; }
  .sign-off--signature { left: 63px; }
  .sign-off--date { left: 561px; }
  .sign-off__line { display: inline-block; width: 187px; height: 2px; background: var(--navy); margin-bottom: 4px; }
  .sign-off--signature .sign-off__line { margin-left: 28px; }
  .sign-off--date .sign-off__line { margin-left: 15px; }
</style>
</head>
<body>
<main class="certificate">
  <svg class="certificate__frame" width="928" height="1200" viewBox="0 0 928 1200">
    <defs>
      <linearGradient id="gold-band" x1="0" x2="1" y1="0" y2="0">
        <stop offset="0" stop-color="#b8862c"/>
        <stop offset=".5" stop-color="#f0cd5e"/>
        <stop offset="1" stop-color="#c99a2e"/>
      </linearGradient>
      <linearGradient id="silver-band" x1="0" x2="1">
        <stop offset="0" stop-color="#7f808e"/>
        <stop offset=".5" stop-color="#a6a7b2"/>
        <stop offset="1" stop-color="#7f808e"/>
      </linearGradient>
      <radialGradient id="pattern-tone" cx=".5" cy=".5" r=".5">
        <stop offset="0" stop-color="#dcdce4" stop-opacity=".9"/>
        <stop offset=".55" stop-color="#e6e6ec" stop-opacity=".7"/>
        <stop offset=".85" stop-color="#eeeef2" stop-opacity=".45"/>
        <stop offset="1" stop-color="#ffffff" stop-opacity="0"/>
      </radialGradient>
      <radialGradient id="compass-tone" cx=".5" cy=".5" r=".5">
        <stop offset="0" stop-color="#8a8ba0" stop-opacity=".85"/>
        <stop offset=".6" stop-color="#6e6f85" stop-opacity=".55"/>
        <stop offset="1" stop-color="#3d3e52" stop-opacity="0"/>
      </radialGradient>
    </defs>

    <ellipse class="background-pattern" role="img" aria-label="Fine guilloche line pattern behind the award text" cx="464" cy="830" rx="470" ry="390" fill="url(#pattern-tone)"/>

    <path d="M0 151 C 180 175, 330 290, 528 282 C 700 275, 840 170, 928 123 L 928 0 L 0 0 Z" fill="url(#gold-band)"/>
    <path d="M0 140 C 180 160, 330 268, 528 262 C 700 256, 840 160, 928 115 L 928 0 L 0 0 Z" fill="url(#silver-band)"/>
    <path d="M0 106 C 180 122, 330 228, 528 226 C 700 222, 840 140, 928 104 L 928 0 L 0 0 Z" fill="var(--navy)"/>

    <ellipse class="header-compass" role="img" aria-label="Faint compass rose in the header, right" cx="855" cy="68" rx="78" ry="70" fill="url(#compass-tone)"/>
    <ellipse class="header-compass" role="img" aria-label="Faint compass rose in the header, left" cx="110" cy="45" rx="105" ry="62" fill="url(#compass-tone)" opacity=".6"/>

    <g class="title-ornament" stroke="#fff" stroke-width="1.5" fill="#fff">
      <line x1="365" y1="190" x2="438" y2="190"/>
      <line x1="490" y1="190" x2="563" y2="190"/>
      <polygon stroke="none" points="464,178 467.5,186.5 476.5,187 469.5,192.5 472,201 464,196 456,201 458.5,192.5 451.5,187 460.5,186.5"/>
    </g>
  </svg>

  <h1 class="certificate__title">CERTIFICATE</h1>
  <p class="certificate__subtitle">OF COMPLETION</p>
  <p class="certificate__anniversary">25th year of existence</p>

  <div class="course-mark">
    <span class="course-mark__square"></span>
    <span class="course-mark__name">Silver Harbour</span>
  </div>

  <p class="award__lead">THIS CERTIFICATE IS AWARDED TO</p>
  <p class="award__recipient">AROHA BENNETT</p>
  <span class="award__rule award__rule--long"></span>
  <span class="award__rule award__rule--short"></span>
  <p class="award__reason">For successfully completing and contributing to the three day<br>Silver Harbour programme.</p>

  <div class="company-mark">
    <span class="company-mark__square"></span>
    <span class="company-mark__name">MELLOR QUAID<br>&amp; ASSOCIATES</span>
  </div>

  <p class="sign-off sign-off--signature">SIGNATURE <span class="sign-off__line"></span></p>
  <p class="sign-off sign-off--date">DATE <span class="sign-off__line"></span></p>
</main>
</body>
</html>
```